Upscale business cards needed for Board of Directors

We need professional business cards created for members of our family business Board of Directors. We would like these relatively simple and straightforward, but also with a unique element to set them apart. Probably stick with neutral and simple colors - white, grey etc. We need space for the traditional elements, including name, title, address, email/phone number. And we will be creating several from this template so it needs to be template that is easy to switch information in and out of.
Business
See description

```html
<!DOCTYPE html>
<html lang="en">
<head>
<meta charset="utf-8">
<title>Harborline Holdings – Business Card</title>
<link href="https://fonts.googleapis.com/css2?family=Roboto:wght@400;500;700&display=swap" rel="stylesheet">
<style>
  :root {
    --backdrop: #e9e6e1;
    --card-white: #ffffff;
    --card-black: #2a2828;
    --gold: #ad9a71;
    --panel-dark: #2e2e2e;
    --panel-mid: #4a4a4a;
    --ink: #2b2b2b;
    --text-light: #ffffff;
  }
  * { box-sizing: border-box; margin: 0; padding: 0; }
  html, body {
    width: 1200px;
    height: 950px;
    overflow: hidden;
    background: var(--backdrop);
    font-family: "Roboto", Arial, sans-serif;
  }
  .stage {
    position: relative;
    width: 1200px;
    height: 950px;
  }

  /* Front of card (portrait) */
  .card-front {
    position: absolute;
    left: 170px;
    top: 170px;
    width: 360px;
    height: 620px;
    background: var(--card-white);
    box-shadow: 0 10px 30px rgba(0,0,0,0.18);
  }
  .name-plate {
    position: absolute;
    left: 28px;
    right: 28px;
    top: 30px;
    height: 100px;
    background: var(--gold);
    color: var(--text-light);
    text-align: center;
    display: flex;
    flex-direction: column;
    justify-content: center;
  }
  .name-plate .person-name {
    font-size: 19px;
    font-weight: 500;
    letter-spacing: 1px;
  }
  .name-plate .person-title {
    font-size: 13px;
    margin-top: 4px;
  }
  .wordmark {
    position: absolute;
    left: 0;
    right: 0;
    top: 300px;
    text-align: center;
    color: var(--ink);
    font-weight: 700;
    line-height: 1;
  }
  .wordmark .line-main {
    font-size: 38px;
    letter-spacing: 1px;
  }
  .wordmark .line-sub {
    font-size: 20px;
    letter-spacing: 9px;
    margin-top: 4px;
  }
  .contact-panel {
    position: absolute;
    left: 28px;
    right: 28px;
    top: 420px;
    height: 170px;
    background: linear-gradient(135deg, var(--panel-mid) 0%, var(--panel-dark) 55%, #1f1f1f 100%);
    color: var(--text-light);
    padding: 26px 0 0 96px;
    font-size: 13px;
    line-height: 1.45;
  }
  .contact-panel .address { margin-bottom: 14px; }
  .contact-panel .label { font-weight: 700; }

  /* Back of card (landscape) */
  .card-back {
    position: absolute;
    left: 590px;
    top: 330px;
    width: 490px;
    height: 280px;
    background: var(--card-black);
    box-shadow: 0 10px 30px rgba(0,0,0,0.22);
    display: flex;
    flex-direction: column;
    justify-content: center;
    align-items: center;
    color: var(--text-light);
    font-weight: 700;
    line-height: 1;
  }
  .card-back .line-main {
    font-size: 46px;
    letter-spacing: 1px;
  }
  .card-back .line-sub {
    font-size: 24px;
    letter-spacing: 11px;
    margin-top: 6px;
  }
</style>
</head>
<body>
<main class="stage">
  <section class="card-front" aria-label="Business card front">
    <div class="name-plate">
      <div class="person-name">MARCUS HALE</div>
      <div class="person-title">President</div>
    </div>
    <div class="wordmark">
      <div class="line-main">HARBORLINE</div>
      <div class="line-sub">HOLDINGS</div>
    </div>
    <div class="contact-panel">
      <div class="address">2170 Kestrel Avenue<br>Brookmere, NY 11020</div>
      <div><span class="label">P:</span> 555 0142 7781</div>
      <div><span class="label">E:</span> marcus@harborline.com</div>
      <div><span class="label">W:</span> www.harborline.com</div>
    </div>
  </section>

  <section class="card-back" aria-label="Business card back">
    <div class="line-main">HARBORLINE</div>
    <div class="line-sub">HOLDINGS</div>
  </section>
</main>
</body>
</html>
```